Harbor Crestline (Business Card Design)

Need business cards designed. Something modern, chic, and sleek. Mabye the back of the card should be the navy blue that is in the logo and then just the logo on the back.

Target Market(s)

Those in the hotel, office, and renovation industry

Contact Information for Business Card

1. Logo 2. Dorian Fenwick 3. CEO/Founder 4. Phone: (833) HarbCre / (833) 427-2731 5. Email: dorian@theharborcrestline.com 6. Website: www.theharborcrestline.com

Font styles to use
Other font styles liked:
• Look at the logo font and base the font for everything else off of that.

Colors
0054AA
0677BA
7BADD7
CADEEF
E8F1F8

Requirements
Must have
• Colors that are associated in the logo
Nice to have
• Sleek modern clean and chic design.

```html
<!DOCTYPE html>
<html lang="en">
<head>
<meta charset="utf-8">
<title>Harbor Crestline — Business Card</title>
<link href="https://fonts.googleapis.com/css2?family=Montserrat:wght@500;700;800&family=Josefin+Sans:wght@400;600&display=swap" rel="stylesheet">
<style>
  :root {
    --navy: #111a42;
    --gold: #d4a537;
    --paper: #ffffff;
    --backdrop: #e4e5e8;
    --ink-soft: #2a2f45;
  }
  * { box-sizing: border-box; margin: 0; padding: 0; }
  html, body { width: 1200px; height: 800px; overflow: hidden; }
  body {
    background: var(--backdrop);
    display: flex;
    align-items: center;
    justify-content: center;
    gap: 40px;
    font-family: "Josefin Sans", sans-serif;
  }
  .card {
    position: relative;
    width: 540px;
    height: 309px;
    overflow: hidden;
    box-shadow: 0 10px 28px rgba(0,0,0,0.14);
  }
  .corner {
    position: absolute;
    width: 22px;
    height: 22px;
    background: var(--gold);
  }
  /* front */
  .card-front { background: var(--paper); color: var(--ink-soft); }
  .card-front .corner-top { top: 0; right: 0; clip-path: polygon(0 0, 100% 0, 100% 100%); }
  .card-front .corner-bottom { bottom: 0; right: 0; clip-path: polygon(100% 0, 100% 100%, 0 100%); }
  .person { position: absolute; left: 40px; top: 34px; }
  .person-name {
    font-family: "Montserrat", sans-serif;
    font-weight: 800;
    font-size: 19px;
    color: var(--navy);
    letter-spacing: 0.5px;
  }
  .person-title { font-size: 15px; color: var(--gold); margin-top: 2px; }
  .contact-list {
    position: absolute; left: 40px; top: 104px;
    list-style: none;
    font-size: 15px;
    line-height: 25px;
  }
  .contact-list li { display: flex; align-items: center; gap: 9px; }
  .contact-list svg { width: 13px; height: 13px; fill: var(--navy); flex: none; }
  .divider-gold {
    position: absolute; left: 40px; top: 192px;
    width: 300px; height: 1px; background: var(--gold);
  }
  .brand-front {
    position: absolute; left: 40px; top: 222px;
    display: flex; align-items: center; gap: 12px;
  }
  .brand-mark { width: 16px; height: 16px; background: var(--gold); }
  .brand-name {
    font-family: "Montserrat", sans-serif;
    font-weight: 700;
    font-size: 28px;
    letter-spacing: 2px;
    text-transform: uppercase;
    color: var(--navy);
  }
  /* back */
  .card-back { background: var(--navy); color: var(--paper); }
  .card-back .corner-top { top: 0; left: 0; clip-path: polygon(0 0, 100% 0, 0 100%); }
  .card-back .corner-bottom { bottom: 0; left: 0; clip-path: polygon(0 0, 100% 100%, 0 100%); }
  .back-content {
    position: absolute; inset: 0;
    display: flex; flex-direction: column; align-items: center; justify-content: center;
  }
  .brand-back { display: flex; align-items: center; gap: 12px; }
  .brand-back .brand-name { color: var(--paper); font-size: 30px; }
  .divider-light { width: 330px; height: 1px; background: rgba(255,255,255,0.75); margin: 18px 0 14px; }
  .website { font-size: 15px; letter-spacing: 1.5px; color: var(--gold); }
</style>
</head>
<body>
  <section class="card card-back" aria-label="Card back">
    <span class="corner corner-top"></span>
    <span class="corner corner-bottom"></span>
    <div class="back-content">
      <div class="brand-back">
        <span class="brand-mark"></span>
        <span class="brand-name">Harbor Crestline</span>
      </div>
      <div class="divider-light"></div>
      <div class="website">www.theharborcrestline.com</div>
    </div>
  </section>

  <section class="card card-front" aria-label="Card front">
    <span class="corner corner-top"></span>
    <span class="corner corner-bottom"></span>
    <div class="person">
      <div class="person-name">DORIAN FENWICK</div>
      <div class="person-title">CEO/Founder</div>
    </div>
    <ul class="contact-list">
      <li>
        <svg viewBox="0 0 24 24" aria-hidden="true"><path d="M6.6 10.8a15.1 15.1 0 0 0 6.6 6.6l2.2-2.2a1 1 0 0 1 1-.25 11.4 11.4 0 0 0 3.6.57 1 1 0 0 1 1 1V20a1 1 0 0 1-1 1A17 17 0 0 1 3 4a1 1 0 0 1 1-1h3.5a1 1 0 0 1 1 1c0 1.25.2 2.45.57 3.57a1 1 0 0 1-.25 1z"/></svg>
        (833) HarbCre / (833) 427-2731
      </li>
      <li>
        <svg viewBox="0 0 24 24" aria-hidden="true"><path d="M2 5h20v14H2zm2 2v.5l8 5 8-5V7zm0 2.8V17h16V9.8l-8 5z"/></svg>
        dorian@theharborcrestline.com
      </li>
      <li>
        <svg viewBox="0 0 24 24" aria-hidden="true"><path d="M12 2a10 10 0 1 0 0 20 10 10 0 0 0 0-20zm6.9 6h-2.9a15 15 0 0 0-1.3-3.6A8 8 0 0 1 18.9 8zM12 4c.8 1.2 1.5 2.5 1.9 4h-3.8c.4-1.5 1.1-2.8 1.9-4zM4.3 14a8 8 0 0 1 0-4h3.4a16 16 0 0 0 0 4zm.8 2h2.9c.3 1.3.8 2.5 1.3 3.6A8 8 0 0 1 5.1 16zM8 8H5.1a8 8 0 0 1 4.2-3.6C8.8 5.5 8.3 6.7 8 8zm4 12c-.8-1.2-1.5-2.5-1.9-4h3.8c-.4 1.5-1.1 2.8-1.9 4zm2.3-6H9.7a14 14 0 0 1 0-4h4.6a14 14 0 0 1 0 4zm.4 5.6c.5-1.1 1-2.3 1.3-3.6h2.9a8 8 0 0 1-4.2 3.6zm1.6-5.6a16 16 0 0 0 0-4h3.4a8 8 0 0 1 0 4z"/></svg>
        www.theharborcrestline.com
      </li>
    </ul>
    <div class="divider-gold"></div>
    <div class="brand-front">
      <span class="brand-mark"></span>
      <span class="brand-name">Harbor Crestline</span>
    </div>
  </section>
</body>
</html>
```